Business Card: RW Office Partners - Your organised problem solver

Business Name: RW Office Partners
Website: www.rwofficepartners.com.au
Email: marisol@rwofficepartners.com.au
Mobile: 61 482 907 236
Facebook: @rwofficepartners
Instrgram: @rwofficepartners

Brading Colours:
HEX
#986474
#ddccd3
#7a8498
#c9d8e4
#000000
#ffffff

Tag Line: Your organised problem solver

Link to DRAFT website:
https://deskhelpcollective.wixsite.com/rw-office-partners

About Page from the website:
My name is Marisol Wrenfield, and I would love to assist you to become more productive in your day to day and achieve your business and personal goals.
My mission is to give you time, time to work on the important tasks of your business or to be able to spend more time with your family. I will take on the tasks you don’t have time for, don’t know well or simply don’t like to do.
I have an extensive background in Administration, Tender Coordination, Document Control, WHS and Quality Management working primarily in the Construction, Mining and Corporate World.
I am passionate about being organised, having order and making things in your life (and mine) easier! I love to watch something unfold and grow into something amazing! I am known for being the go-to problem solver, the organiser of all things, producing high standards of work even under pressure. I’m also a confident communicator, and I understand that you’re busy running your business.

Target Market(s)

Small to Medium Business who require assistance in their business by a virtual assistant.

Industry/Entity Type

Virtual Assistant

Contact Information for Business Card

Mobile: 61 482 907 236

Font styles to use
Sans Serif

Colors
ffffff

Requirements
Must have
• Branding Colours as outlined.
Contact Details as outlined.
Logo as provided.
Proper contact details - mobile, facebook, instragm, website.
Simple, Elegant, very clean looking.
Should not have
• Note cute with pictures.
Not too girly as still want to market to construction companies.

```html
<!DOCTYPE html>
<html lang="en">
<head>
<meta charset="utf-8">
<title>RW Office Partners – Business Card</title>
<link rel="stylesheet" href="https://fonts.googleapis.com/css2?family=Montserrat:wght@400;500;600;700&display=swap">
<style>
  :root {
    --backdrop: #3b3532;
    --card: #0b0b0b;
    --mauve: #986474;
    --blush: #ddccd3;
    --slate: #7a8498;
    --mist: #c9d8e4;
    --white: #ffffff;
    --rule: #4a4a4a;
  }
  * { box-sizing: border-box; margin: 0; padding: 0; }
  html, body {
    width: 1200px; height: 844px; overflow: hidden;
    background: var(--backdrop);
    font-family: "Montserrat", Arial, sans-serif;
  }
  .stage {
    position: relative; width: 1200px; height: 844px;
    display: flex; align-items: center; justify-content: center; gap: 60px;
  }
  .card {
    position: relative; width: 520px; height: 300px;
    background: var(--card);
    box-shadow: 0 14px 30px rgba(0,0,0,.45);
  }
  /* Front */
  .card-front .brand {
    position: absolute; top: 52px; right: 44px;
    display: flex; align-items: center; gap: 12px;
  }
  .brand-dot {
    width: 14px; height: 14px; border-radius: 50%;
    background: var(--mauve);
  }
  .brand-name {
    font-weight: 600; font-size: 26px; letter-spacing: .5px;
    color: var(--mauve);
  }
  .card-front .divider {
    position: absolute; top: 120px; left: 44px; right: 44px;
    height: 1px; background: var(--rule);
  }
  .social {
    position: absolute; top: 140px; right: 44px;
    display: flex; align-items: center; gap: 8px;
    color: var(--mist); font-size: 14px;
  }
  .social-dot {
    width: 16px; height: 16px; border-radius: 50%;
    border: 1px solid var(--mist);
  }
  .holder {
    position: absolute; left: 44px; top: 190px;
    font-weight: 700; font-size: 17px; letter-spacing: .5px;
    text-transform: uppercase; color: var(--mauve);
  }
  .contacts {
    position: absolute; left: 44px; top: 222px;
    list-style: none; display: grid; gap: 6px;
    color: var(--mist); font-size: 13px;
  }
  .contacts li { display: flex; align-items: center; gap: 9px; }
  .contacts svg { width: 13px; height: 13px; flex: none; }
  /* Back */
  .card-back {
    display: flex; flex-direction: column; align-items: center; justify-content: center; gap: 46px;
  }
  .card-back .brand-name { color: var(--white); font-size: 30px; }
  .tagline {
    font-weight: 700; font-size: 12px; letter-spacing: .6px;
    text-transform: uppercase; color: var(--white);
  }
</style>
</head>
<body>
<main class="stage">
  <section class="card card-front" aria-label="Card front">
    <div class="brand">
      <span class="brand-dot"></span>
      <span class="brand-name">RW Office Partners</span>
    </div>
    <div class="divider"></div>
    <div class="social"><span class="social-dot"></span><span>@rwofficepartners</span></div>
    <h1 class="holder">Marisol Wrenfield</h1>
    <ul class="contacts">
      <li>
        <svg viewBox="0 0 16 16" aria-hidden="true"><path fill="#986474" d="M3 1h3l1.5 4-2 1.3a9 9 0 0 0 4.2 4.2L11 8.5l4 1.5v3a2 2 0 0 1-2 2A12 12 0 0 1 1 3a2 2 0 0 1 2-2z"/></svg>
        <span>61 482 907 236</span>
      </li>
      <li>
        <svg viewBox="0 0 16 16" aria-hidden="true"><rect x="1" y="3" width="14" height="10" fill="#986474"/><path d="M1.5 3.5 8 9l6.5-5.5" stroke="#0b0b0b" stroke-width="1.3" fill="none"/></svg>
        <span>marisol@rwofficepartners.com.au</span>
      </li>
      <li>
        <svg viewBox="0 0 16 16" aria-hidden="true"><circle cx="8" cy="8" r="7" fill="#986474"/><path d="M1 8h14M8 1c3 3 3 11 0 14M8 1c-3 3-3 11 0 14" stroke="#0b0b0b" stroke-width="1" fill="none"/></svg>
        <span>www.rwofficepartners.com.au</span>
      </li>
    </ul>
  </section>

  <section class="card card-back" aria-label="Card back">
    <div class="brand">
      <span class="brand-name">RW Office Partners</span>
    </div>
    <p class="tagline">Your organised problem solver</p>
  </section>
</main>
</body>
</html>
```